Paths to Delight E-card design - Potential for other work

I am looking for a designer to create e card, thank you design templates for my new not for profit website www.pathstodelight.com.au.

They will have simple imagery, with a subtle and soft illustration which reflects some sort of emotion. Think of patterns and textures.

The main focus of the card will be the text submitted as the "Path to Delight". For an example of the text please see http://www.pathstodelight.com.au/search-for-ideas/.

The width of the card / image (which will be displayed on a web page) will be 700px max, and there is no restriction on height.

The colours will be similar to the website colours although possibly softer/pastal colours.

The design should contain a header/title "You've amazed me, thank you" before the actual words merged from the site as the Path to Delight. It will appear on a blank page on the website with the same header so it doesn't have to be similar to the website design.

I will upload similar designs I like to make your job easier on Monday.

Although this job is only for a couple of simple designs, I will require more in the future so there is potential for ongoing work. I am therefore looking for a provider who is reliable, trustworthy, efficient and of course has a creative design flair.

If you want to be a part of a great cause, please submit your designs. I look forward to working with you.

Thank you.

Target Market(s)

Everyone with a kind heart ;0)

Industry/Entity Type

Work

Requirements
Nice to have
• In terms of the attached files, 1 and 2 give an example of a pattern that is quite nice. Number 4 shows the colours I quite like with the orange. We want the e card to evoke emotion. (please note the design Is for an e card, not business card. This is just an example of a design, please ignore the fact it is on a business card.
Should not have
• Too much going on

```html
<!DOCTYPE html>
<html lang="en">
<head>
<meta charset="utf-8">
<title>Paths to Delight – Thank You Card</title>
<link rel="stylesheet" href="https://fonts.googleapis.com/css2?family=Fira+Sans:ital,wght@0,700;1,700&family=Open+Sans:wght@400&display=swap">
<style>
  :root {
    --stage: #1b1b1b;
    --paper: #eeeeee;
    --ink: #3f3f3f;
    --ink-soft: #2e2e2e;
    --orange: #ef6223;
    --swoosh-dark: #1e1e1e;
    --swoosh-mid: #8a8a8a;
    --white: #ffffff;
  }
  * { box-sizing: border-box; margin: 0; padding: 0; }
  html, body {
    width: 1200px; height: 404px; overflow: hidden;
    background: var(--stage);
  }
  .stage { position: relative; width: 1200px; height: 404px; }
  .card {
    position: absolute; top: 64px;
    width: 496px; height: 284px;
    background: var(--paper);
    border-radius: 15px;
    overflow: hidden;
  }
  .card--front { left: 93px; }
  .card--back { left: 632px; }

  .card__title {
    position: absolute; left: 0; right: 0;
    text-align: center;
    font-family: "Fira Sans", sans-serif;
    font-weight: 700; font-style: italic;
    color: var(--ink);
  }
  .card--front .card__title { top: 21px; font-size: 16.5px; transform: translateX(6px); }
  .card--back .card__title { top: 84px; font-size: 21px; }

  .brand-name {
    position: absolute; left: 0; right: 0;
    text-align: center;
    font-family: "Fira Sans", sans-serif;
    font-weight: 700;
    color: var(--orange);
    line-height: 1;
  }
  .card--front .brand-name { top: 78px; font-size: 32px; transform: translateX(6px); }
  .card--back .brand-name { top: 150px; font-size: 38px; }

  .contact {
    position: absolute; top: 181px; left: 0; width: 496px;
    font-family: "Open Sans", sans-serif;
    font-size: 12px; color: var(--ink-soft); line-height: 16px;
  }
  .contact__address {
    position: absolute; right: 252px; top: 9px; text-align: right;
  }
  .contact__divider {
    position: absolute; left: 250px; top: 2px;
    width: 1px; height: 48px; background: #b5b5b5;
  }
  .contact__lines { position: absolute; left: 259px; top: 0; list-style: none; }
  .contact__lines li { display: flex; align-items: center; gap: 5px; }
  .contact__lines svg { width: 9px; height: 9px; fill: var(--ink-soft); }

  .card__wave { position: absolute; left: 0; top: 0; }
  .card__url {
    position: absolute; left: 43px; top: 266px;
    font-family: "Open Sans", sans-serif;
    font-size: 15px; letter-spacing: 1.6px;
    color: var(--white);
  }
</style>
</head>
<body>
<main class="stage">
  <section class="card card--front">
    <h1 class="card__title">You've amazed me, thank you</h1>
    <p class="brand-name">Paths to Delight</p>

    <div class="contact">
      <address class="contact__address" style="font-style:normal">123 XYZ ST.<br>My City, Ca 12346</address>
      <span class="contact__divider"></span>
      <ul class="contact__lines">
        <li><svg viewBox="0 0 10 10"><path d="M2 0.5 L4 2.8 L3 4 Q4.2 6 6 7 L7.2 6 L9.5 8 L8 9.6 Q3.5 9 0.4 2 Z"/></svg>312-555-0148</li>
        <li><svg viewBox="0 0 10 10"><rect x="2" y="0.5" width="6" height="9" rx="1"/></svg>123-456-789</li>
        <li><svg viewBox="0 0 10 10"><path d="M0.5 2 H9.5 V8.5 H0.5 Z"/></svg>name@website.com</li>
      </ul>
    </div>

    <svg class="card__wave" width="496" height="284" viewBox="0 0 496 284" aria-hidden="true">
      <defs>
        <linearGradient id="swoosh" x1="0" y1="0" x2="1" y2="0">
          <stop offset="0" stop-color="var(--swoosh-dark)"/>
          <stop offset="0.55" stop-color="var(--swoosh-dark)"/>
          <stop offset="1" stop-color="var(--swoosh-mid)"/>
        </linearGradient>
      </defs>
      <path d="M0 218 C110 214 220 232 290 256 C350 276 420 258 496 228 L496 236 C430 262 360 282 292 266 C220 244 110 232 0 232 Z" fill="url(#swoosh)"/>
      <path d="M0 240 C110 238 210 250 280 268 C350 284 430 268 496 244 L496 284 L0 284 Z" fill="var(--orange)"/>
    </svg>
    <p class="card__url">www.website.com</p>
  </section>

  <section class="card card--back">
    <h2 class="card__title">You've amazed me, thank you</h2>
    <p class="brand-name">Paths to Delight</p>
  </section>
</main>
</body>
</html>
```